Website visual upgrade

I am seeking expressions of interest for the updating the visuals of my website www.kelvastaffing.net
I am basically seeking a simple,bold and visually strong graphic makeover.using existing or shortly to be modified text.

```html
<!DOCTYPE html>
<html lang="en">
<head>
<meta charset="utf-8">
<title>Kelva Staffing</title>
<link rel="stylesheet" href="https://fonts.googleapis.com/css2?family=Source+Sans+3:wght@400;600;700&family=Arimo:wght@400&display=swap">
<style>
:root{
  --red:#c8102e;
  --ink:#1f1f1f;
  --text:#555;
  --nav:#222;
  --footer:#3a3a3a;
  --bg:#fff;
}
*{margin:0;padding:0;box-sizing:border-box}
html,body{width:1125px;height:1200px;overflow:hidden;background:var(--bg)}
body{position:relative;font-family:"Source Sans 3",sans-serif;color:var(--text)}
.abs{position:absolute}
.brand{left:112px;top:30px;display:flex;align-items:center;gap:12px}
.brand-dot{width:30px;height:30px;border-radius:50%;background:var(--ink)}
.brand-name{font-size:34px;font-weight:700;color:var(--red);letter-spacing:.5px}
.call{right:113px;top:46px;display:flex;align-items:center;gap:8px;font-family:Arimo,sans-serif;font-size:12.5px;color:#222}
.call b{font-weight:400;color:var(--red)}
.nav{left:112px;top:105px;width:901px;height:41px;background:var(--nav);display:flex;align-items:stretch;padding-right:9px;justify-content:space-between;box-shadow:0 2px 3px rgba(0,0,0,.25)}
.nav a{color:#fff;text-decoration:none;font-size:13px;font-weight:600;display:flex;align-items:center;padding:0 0px}
.nav a.active{background:var(--red);padding:0 9px}
.hero{left:0;top:146px;width:1125px;height:374px;background:linear-gradient(90deg,#d9dde0 0%,#5b4a3e 20%,#202020 45%,#e7e4de 58%,#2a2420 80%,#e6e3df 100%)}
.dots{left:516px;top:502px;height:18px;width:86px;background:#aaa;border-radius:9px 9px 0 0;display:flex;align-items:center;justify-content:center;gap:4px}
.dots i{width:10px;height:10px;border-radius:50%;background:#666;border:1px solid #eee}
.dots i.on{background:#222}
h2{position:absolute;font-size:16.5px;font-weight:600;color:var(--ink)}
h2 span{color:var(--red)}
.photo{position:absolute;box-shadow:0 1px 2px rgba(0,0,0,.3)}
.copy{position:absolute;font-size:12.3px;line-height:15.8px;text-align:justify}
.copy p+p{margin-top:15.8px}
.more{position:absolute;width:86px;height:31px;background:var(--ink);color:#fff;font-size:12.5px;font-weight:600;padding:7px 0 0 8px;clip-path:polygon(0 0,88% 0,100% 50%,88% 100%,0 100%)}
.divider{left:112px;top:836px;width:903px;height:6px;background:linear-gradient(#fff,#eee);box-shadow:0 3px 4px rgba(0,0,0,.08)}
.areas{left:731px;top:904px;width:282px;font-size:12.3px;line-height:15px}
.areas ul{list-style:none;margin-top:10px;font-size:11px}
.areas li{height:17.8px;padding-left:19px;position:relative}
.areas li:before{content:"";position:absolute;left:1px;top:4px;border-left:4px solid var(--red);border-top:3px solid transparent;border-bottom:3px solid transparent}
.footer{left:0;top:1151px;width:1125px;height:49px;background:var(--footer);color:#fff;font-family:Arimo,sans-serif;font-size:11.5px}
.footer .legal{position:absolute;left:112px;top:19px}
.social{position:absolute;left:850px;top:15px;display:flex;gap:8px}
.social i{width:22px;height:22px}
</style>
</head>
<body>
<div class="abs brand"><span class="brand-dot"></span><span class="brand-name">Kelva Staffing</span></div>
<div class="abs call">
  <svg width="12" height="18" viewBox="0 0 12 18"><path d="M4 1 C0 4 0 14 4 17 L7 15 L5 11 C4 9 4 9 5 7 L7 3 Z" fill="var(--red)"/></svg>
  <span>CALL US NOW! <b>1300 555 018</b></span>
</div>
<nav class="abs nav">
  <a class="active" href="#">HOME</a><a href="#">WHO WE ARE</a><a href="#">OUR APPROACH</a><a href="#">WHAT WE DO</a><a href="#">MIGRATION</a><a href="#">ASSISTANCE</a><a href="#">JOB SEEKER</a><a href="#">USEFUL LINKS</a><a href="#">SUPPORT</a><a href="#">CONTACT US</a>
</nav>
<div class="abs hero" role="img" aria-label="Three business people in dark suits reviewing documents at a desk"></div>
<div class="abs dots"><i></i><i></i><i class="on"></i><i></i><i></i><i></i></div>

<h2 style="left:112px;top:536px">Welcome to <span>Kelva Staffing!</span></h2>
<div class="photo" style="left:113px;top:578px;width:225px;height:188px;background:linear-gradient(120deg,#eef0f2,#b8b4ae 50%,#f0e8e4)" role="img" aria-label="Business people shaking hands in an office"></div>
<div class="copy" style="left:347px;top:576px;width:356px">
  <p>We are committed to providing the highest standards of service in Executive search and selection and the provision of Skilled trades people and allied Health professionals throughout Australia.</p>
  <p>We have offices throughout Australia, clearly adding value to our clients’ strategic needs, wherever they may be. Competing organisations have access to similar Technology, Raw Materials and Human Capital.</p>
  <p>The ability to identify, attract and retain quality personnel will clearly differentiate those organisations which are successful and develop a corporate culture of excellence and innovation.</p>
</div>
<div class="more" style="left:112px;top:783px">Read More</div>

<h2 style="left:731px;top:536px">Our history</h2>
<div class="photo" style="left:731px;top:578px;width:282px;height:113px;background:linear-gradient(#3f78c8,#8cb2e0 45%,#6a6a6a 75%,#9a8a74)" role="img" aria-label="City skyline under a blue sky"></div>
<div class="copy" style="left:731px;top:694px;width:282px;height:70px;overflow:hidden;font-size:11.5px;line-height:14.7px">
  <p>Our firm is proudly 100% Australian owned and operated. We have excellent alliance partners in South Africa, The Philippines, New Zealand and the UK.We commenced operations in Melbourne in 1992 and have grown nationally with offices in Melbourne, Brisbane,</p>
</div>
<div class="more" style="left:731px;top:783px">Read More</div>

<div class="abs divider"></div>

<h2 style="left:112px;top:862px">Our Culture</h2>
<div class="photo" style="left:113px;top:905px;width:281px;height:112px;background:linear-gradient(90deg,#d9c9a0,#7f8ea3 45%,#c9c9c9)" role="img" aria-label="Engineers in hard hats talking on a work site"></div>
<div class="copy" style="left:112px;top:1028px;width:282px;font-size:11.5px;line-height:14.7px">
  <p>We think laterally about our clients’ needs and deliver a “fresh approach” to Executive search and selection and the provision of Skilled trades people and allied Health recruitment.</p>
</div>
<div class="more" style="left:112px;top:1100px">Read More</div>

<h2 style="left:421px;top:862px">Migration assistance</h2>
<div class="photo" style="left:421px;top:905px;width:281px;height:112px;background:linear-gradient(90deg,#2a3f9a,#c8283a 30%,#2a3f9a 55%,#e8d8c8 75%,#3050b0)" role="img" aria-label="Smiling woman holding a certificate in front of a flag"></div>
<div class="copy" style="left:421px;top:1028px;width:282px;font-size:11.5px;line-height:14.7px">
  <p>We think laterally about our clients’ needs and deliver a “fresh approach” to Executive search and selection and the provision of Skilled trades people and allied Health recruitment.</p>
</div>
<div class="more" style="left:421px;top:1100px">Read More</div>

<h2 style="left:731px;top:862px">Our specialist areas</h2>
<div class="abs areas">
  <p>We are Executive search and selection specialists in the following areas:</p>
  <ul>
    <li>Accounting and Corporate Finance</li><li>Engineering</li><li>Health and Allied Heath</li><li>Local Government</li><li>Manufacturing</li><li>Mining</li><li>Oil &amp; Gas</li><li>Skilled trades people</li>
  </ul>
</div>
<div class="more" style="left:731px;top:1100px">Read More</div>

<footer class="abs footer">
  <div class="legal">© 2013 Kelva Partners| &nbsp;Privacy Notice &nbsp; | &nbsp;Conditions of Use</div>
  <div class="social">
    <i style="background:#3b5998"></i><i style="background:#2aa9e0"></i><i style="background:#222"></i><i style="background:#cb2027"></i><i style="background:#d8261f"></i><i style="background:#f39a1e"></i>
  </div>
</footer>
</body>
</html>
```